Online training business needs new website

We need a new wordpress website as a result of a rebranding. The business is a crisis management training company focussed on online training and simulation exercises. We only need a 4 page site - home, about us, contact us and blog. However we must be able to add additional tabs in the header to redirect to our sales and marketing system (Kartra). As these change from time to time, we must be able to add and delete as required.The site must be editable by us, with a basic understanding of wordpress and no understanding of coding. We don't want to have to employ someone to change text, add posts or add a new workshops etc. The theme chosen must be easy to edit by a beginner.

Target Market(s)

Senior managers food and consumer goods companies

Industry/Entity Type

Consulting

Coding

Coded - Design and coding required

Font styles to use
Sans Serif

Requirements
Must have
• Home page, about us, contact us, blog
• Colour scheme from logo (attached) - maroon, blue and grey
• If you go to the current website "tidewellcollege.com" and click on the "workshops" tab you will see the content I need on the home page for the plumvantage.com site
Nice to have
• Modern, simple and minimalist design is preferred

```html
<!DOCTYPE html>
<html lang="en">
<head>
<meta charset="utf-8">
<title>Plum Vantage — Workshops &amp; Simulations</title>
<link href="https://fonts.googleapis.com/css2?family=Roboto:wght@400;500;700;900&display=swap" rel="stylesheet">
<style>
:root{
  --maroon:#8c1c42;
  --maroon-dark:#6e1232;
  --navy:#1d3a6b;
  --navy-dark:#17305a;
  --grey:#6b6f76;
  --grey-light:#f1f4f8;
  --line:#d9dde3;
  --text:#3a3d42;
  --white:#ffffff;
  --star:#e3b21a;
}
*{box-sizing:border-box;margin:0;padding:0}
html,body{width:1200px;height:4932px;overflow:hidden}
body{font-family:'Roboto',Arial,sans-serif;color:var(--text);background:var(--white);position:relative}
section,header,footer{position:relative;width:1200px;overflow:hidden}
.btn{display:inline-block;border-radius:40px;font-weight:700;font-size:15px;text-transform:uppercase;text-align:center;text-decoration:none;letter-spacing:.3px}
.btn-solid{background:var(--maroon);color:var(--white);padding:12px 30px}
.btn-outline{border:2px solid var(--maroon);color:var(--maroon);padding:13px 40px;background:var(--white)}
.section-title{font-weight:900;text-transform:uppercase;text-align:center;color:var(--navy);font-size:36px;letter-spacing:.5px}

/* header */
.site-header{height:115px;background:var(--white)}
.brand{position:absolute;left:170px;top:18px;display:flex;align-items:center;gap:12px}
.brand-mark{width:72px;height:72px;border-radius:50%;background:var(--maroon)}
.brand-name{font-weight:900;font-size:28px;line-height:1;color:var(--maroon);text-transform:uppercase}
.top-note{position:absolute;left:618px;top:20px;font-size:12px;font-weight:700;color:var(--navy)}
.header-register{position:absolute;left:920px;top:9px;width:110px;height:40px;line-height:40px;background:var(--navy);color:var(--white);border-radius:20px;font-size:13px;padding:0}
.main-nav{position:absolute;left:368px;top:66px;display:flex;gap:28px}
.main-nav a{font-size:15px;font-weight:500;color:var(--navy);text-decoration:none;text-transform:uppercase}

/* hero */
.hero{height:592px}
.hero-photo{position:absolute;inset:0;background:linear-gradient(180deg,#6f737a 0%,#4e535b 55%,#3b3f47 100%)}
.hero-content{position:absolute;top:170px;left:0;width:100%;text-align:center}
.hero-title{color:var(--white);font-size:40px;font-weight:900;line-height:1.15;text-transform:uppercase;text-shadow:0 2px 6px rgba(0,0,0,.35)}
.hero-actions{margin-top:38px;display:flex;justify-content:center;gap:14px}
.hero-actions .btn{text-transform:none;font-size:16px;padding:12px 32px;line-height:1.2;border-radius:36px;color:var(--white)}
.btn-navy{background:var(--navy)}
.btn-maroon{background:var(--maroon)}
.hero-curve{position:absolute;left:0;bottom:0;width:1200px;height:130px}

/* intro */
.intro{height:243px;text-align:center;padding:40px 250px 0}
.intro p{font-size:18px;line-height:1.4;color:var(--grey);margin-bottom:16px}

/* stats */
.stats{height:415px}
.stat-grid{position:absolute;left:158px;top:20px;display:grid;grid-template-columns:435px 435px;gap:18px 13px}
.stat-card{height:172px;border:1px solid var(--line);box-shadow:0 2px 8px rgba(0,0,0,.06);display:flex;align-items:center;padding:0 24px;gap:24px;background:var(--white)}
.stat-card svg{flex:0 0 92px}
.stat-card p{font-size:17px;line-height:1.4;color:var(--navy)}

/* steps */
.steps{height:675px;background:var(--grey-light)}
.steps .section-title{position:absolute;top:110px;left:0;width:100%;font-size:28px;line-height:1.35}
.step-row{position:absolute;top:220px;left:0;width:100%;height:320px}
.step{position:absolute;top:0;width:300px;text-align:center}
.step-circle{width:184px;height:184px;margin:0 auto;border:5px solid var(--navy);border-radius:50%;background:var(--white);display:flex;align-items:center;justify-content:center}
.step h3{margin-top:28px;font-size:21px;font-weight:700;color:var(--navy)}
.step p{margin-top:10px;font-size:12px;line-height:1.5;color:var(--grey);padding:0 20px}
.step-arrow{position:absolute;top:80px}
.steps .btn{position:absolute;top:580px;left:335px;width:530px;padding:14px 0}

/* reviews */
.reviews{height:420px}
.reviews-band{position:absolute;inset:0}
.reviews .section-title{position:absolute;top:88px;width:100%;color:var(--white);font-size:30px}
.review-card{position:absolute;top:188px;width:280px;display:flex;gap:14px}
.avatar{flex:0 0 70px;height:70px;border-radius:50%;background:linear-gradient(135deg,#c9a489,#7d5a48);border:3px solid var(--white)}
.review-card blockquote{font-size:11px;line-height:1.45;color:var(--white)}
.review-card cite{display:block;margin-top:10px;font-style:normal;font-weight:700;font-size:13px;color:var(--white)}
.stars{margin-top:8px;display:flex;gap:3px}
.review-nav{position:absolute;top:372px;left:572px;display:flex;gap:4px}
.review-nav span{width:24px;height:24px;border:1.5px solid var(--white);border-radius:50%;display:flex;align-items:center;justify-content:center}

/* workshops */
.workshops{height:697px}
.workshops .section-title{position:absolute;top:85px;width:100%}
.workshop-card{position:absolute;top:160px;width:279px;height:355px;border:1px solid var(--line);box-shadow:0 2px 10px rgba(0,0,0,.08);text-align:center;background:var(--white)}
.workshop-photo{margin:18px 18px 0;height:160px}
.workshop-card h3{margin-top:26px;font-size:21px;font-weight:700;color:#222}
.workshop-card p{margin:12px 22px 0;font-size:12px;line-height:1.5;color:var(--grey)}
.workshop-card .btn{position:absolute;bottom:-2px;left:50%;transform:translateX(-50%);font-size:12px;padding:11px 24px;bottom:0;margin-bottom:-10px}
.workshops .btn-outline{position:absolute;top:588px;left:447px;width:306px;padding:14px 0}

/* simulations */
.simulations{height:658px}
.sim-illustration{position:absolute;left:148px;top:80px;width:380px;height:410px;border-radius:30px;background:linear-gradient(160deg,#2f3a4a 0%,#e85a7e 60%,#f4a68e 100%)}
.sim-title{position:absolute;left:575px;top:98px;font-size:34px;font-weight:900;color:var(--navy);text-transform:uppercase}
.sim-sub{position:absolute;left:575px;top:150px;font-size:16px;color:var(--grey)}
.sim-item{position:absolute;left:570px;width:520px;display:flex;gap:28px;align-items:flex-start}
.sim-icon{flex:0 0 76px;height:76px;border-radius:50%;border:3px solid var(--line);background:var(--white);display:flex;align-items:center;justify-content:center}
.sim-icon span{width:48px;height:48px;border-radius:50%;background:var(--navy);display:flex;align-items:center;justify-content:center}
.sim-item h3{font-size:18px;font-weight:700;color:#222;margin-top:6px}
.sim-item p{margin-top:8px;font-size:12px;line-height:1.5;color:var(--grey);width:330px}
.simulations .btn-outline{position:absolute;top:570px;left:487px;width:204px;padding:14px 0}

/* different */
.different{height:510px}
.different-band{position:absolute;inset:0}
.different h2{position:absolute;left:170px;top:130px;font-size:30px;font-weight:900;color:var(--white);text-transform:uppercase}
.different p{position:absolute;left:170px;top:182px;width:420px;font-size:15px;line-height:1.5;color:#dbe3f0}
.different .btn{position:absolute;left:170px;top:338px;border:2px solid var(--white);color:var(--white);padding:14px 48px}
.different-photo{position:absolute;left:618px;top:115px;width:441px;height:280px;border:4px solid var(--maroon);background:linear-gradient(135deg,#cdb9a5,#6d5a4d)}

/* contact */
.contact{height:445px}
.contact .section-title{position:absolute;top:65px;width:100%;color:#222;font-size:32px}
.contact-form{position:absolute;left:263px;top:130px;width:684px;display:grid;grid-template-columns:1fr 1fr;gap:13px 12px}
.field{height:40px;border:1px solid #c8cdd4;padding:0 14px;font-size:13px;color:var(--grey);display:flex;align-items:center}
.field-wide{grid-column:1/3;height:84px;align-items:flex-start;padding-top:12px}
.contact .btn{position:absolute;top:340px;left:535px;width:130px;padding:13px 0}

/* footer */
.site-footer{height:162px;background:var(--grey-light);text-align:center}
.footer-nav{padding-top:52px;display:flex;justify-content:center;gap:26px}
.footer-nav a{font-size:15px;font-weight:500;color:var(--navy);text-decoration:none;text-transform:uppercase}
.copyright{margin-top:14px;font-size:15px;color:var(--grey)}
</style>
</head>
<body>

<header class="site-header">
  <div class="brand"><span class="brand-mark"></span><span class="brand-name">Plum Vantage</span></div>
  <div class="top-note">NEXT WORK SHOP - SYDNEY , MELBOURNE</div>
  <a class="btn header-register" href="#">Register</a>
  <nav class="main-nav">
    <a href="#">About us</a><a href="#">Workshops</a><a href="#">Online course</a><a href="#">Simulations</a><a href="#">Contact us</a><a href="#">Blog</a>
  </nav>
</header>

<section class="hero">
  <div class="hero-photo" role="img" aria-label="Photo of business people in a meeting around a table"></div>
  <div class="hero-content">
    <h1 class="hero-title">Workshops &amp; Simulations to<br>help food and consumer goods<br>companies prevent a crisis</h1>
    <div class="hero-actions">
      <a class="btn btn-navy" href="#">Register for a<br>workshop</a>
      <a class="btn btn-maroon" href="#">Download our free guide to<br>crisis preventio</a>
    </div>
  </div>
  <svg class="hero-curve" viewBox="0 0 1200 130" aria-hidden="true">
    <path d="M0 60 Q600 150 1200 60 L1200 130 L0 130 Z" fill="#fff"/>
    <path d="M0 56 Q600 146 1200 56" fill="none" stroke="#1d3a6b" stroke-width="6"/>
    <path d="M0 68 Q600 158 1200 68" fill="none" stroke="#8c1c42" stroke-width="3"/>
    <circle cx="600" cy="100" r="30" fill="#fff" stroke="#1d3a6b" stroke-width="3"/>
  </svg>
</section>

<section class="intro">
  <p>When customers stop buying your product - and influence others to do the same, that's a brand crisis!</p>
  <p>If you are a food or consumer goods manufacturer, distributor or retailer, your relationship with customers is the basis of your business - but it can be fragile.</p>
  <p>When an incident happens or product recall may be necessary, your reputation is on the line. Social media will spread the message fast</p>
</section>

<section class="stats">
  <div class="stat-grid">
    <div class="stat-card">
      <svg width="92" height="92" viewBox="0 0 92 92" aria-hidden="true"><path d="M46 6 A40 40 0 1 0 86 46" fill="none" stroke="#d9dde3" stroke-width="5"/><text x="46" y="56" text-anchor="middle" font-size="30" font-weight="700" fill="#8c1c42" font-family="Roboto,sans-serif">$</text></svg>
      <p>The average cost of a crisis is $10m and 25% cost over $100m</p>
    </div>
    <div class="stat-card">
      <svg width="92" height="92" viewBox="0 0 92 92" aria-hidden="true"><path d="M46 6 A40 40 0 1 0 86 46" fill="none" stroke="#d9dde3" stroke-width="5"/><polyline points="26,36 38,48 48,40 60,56 68,52" fill="none" stroke="#8c1c42" stroke-width="3"/></svg>
      <p>Small and medium size businesses often don't survive at all</p>
    </div>
    <div class="stat-card">
      <svg width="92" height="92" viewBox="0 0 92 92" aria-hidden="true"><path d="M46 6 A40 40 0 1 0 86 46" fill="none" stroke="#d9dde3" stroke-width="5"/><rect x="30" y="30" width="32" height="32" rx="4" fill="none" stroke="#8c1c42" stroke-width="3"/><path d="M38 38 L54 54 M54 38 L38 54" stroke="#8c1c42" stroke-width="3"/></svg>
      <p>The largest cost to any size business is to your reputation &amp; brand - that impacts customer relationships &amp; long term sales!</p>
    </div>
    <div class="stat-card">
      <svg width="92" height="92" viewBox="0 0 92 92" aria-hidden="true"><path d="M46 6 A40 40 0 1 0 86 46" fill="none" stroke="#d9dde3" stroke-width="5"/><path d="M46 26 L68 64 L24 64 Z" fill="none" stroke="#8c1c42" stroke-width="3"/><path d="M46 40 V52" stroke="#8c1c42" stroke-width="3"/><circle cx="46" cy="58" r="2" fill="#8c1c42"/></svg>
      <p>Reputation risk remains the number one concern of senior executives, but most are unprepared for a crisis</p>
    </div>
  </div>
</section>

<section class="steps">
  <h2 class="section-title">A crisis can be prevented - but you need to be prepared<br>we prepare your team in 3 easy steps</h2>
  <div class="step-row">
    <div class="step" style="left:113px">
      <div class="step-circle"><svg width="70" height="80" viewBox="0 0 70 80" aria-hidden="true"><circle cx="35" cy="30" r="22" fill="none" stroke="#8c1c42" stroke-width="3"/><rect x="26" y="54" width="18" height="14" fill="none" stroke="#8c1c42" stroke-width="3"/></svg></div>
      <h3>Create your plan</h3>
      <p>We map your key risks and write a clear response plan your team can follow.</p>
    </div>
    <svg class="step-arrow" style="left:390px" width="110" height="24" viewBox="0 0 110 24" aria-hidden="true"><path d="M0 12 H100 M88 4 L100 12 L88 20 M80 4 L92 12 L80 20" fill="none" stroke="#1d3a6b" stroke-width="3"/></svg>
    <div class="step" style="left:425px">
      <div class="step-circle"><svg width="80" height="70" viewBox="0 0 80 70" aria-hidden="true"><circle cx="40" cy="20" r="11" fill="none" stroke="#8c1c42" stroke-width="3"/><circle cx="16" cy="28" r="8" fill="none" stroke="#8c1c42" stroke-width="3"/><circle cx="64" cy="28" r="8" fill="none" stroke="#8c1c42" stroke-width="3"/><path d="M22 62 Q40 30 58 62 M4 60 Q16 40 28 52 M52 52 Q64 40 76 60" fill="none" stroke="#8c1c42" stroke-width="3"/></svg></div>
      <h3>Train your people</h3>
      <p>Hands-on sessions build the skills and confidence to act fast under pressure.</p>
    </div>
    <svg class="step-arrow" style="left:702px" width="110" height="24" viewBox="0 0 110 24" aria-hidden="true"><path d="M0 12 H100 M88 4 L100 12 L88 20 M80 4 L92 12 L80 20" fill="none" stroke="#1d3a6b" stroke-width="3"/></svg>
    <div class="step" style="left:738px">
      <div class="step-circle"><svg width="80" height="70" viewBox="0 0 80 70" aria-hidden="true"><circle cx="30" cy="36" r="16" fill="none" stroke="#8c1c42" stroke-width="6" stroke-dasharray="6 4"/><circle cx="30" cy="36" r="6" fill="none" stroke="#8c1c42" stroke-width="3"/><circle cx="60" cy="22" r="10" fill="none" stroke="#8c1c42" stroke-width="5" stroke-dasharray="4 3"/></svg></div>
      <h3>Practice your process</h3>
      <p>Realistic exercises test the plan so gaps are found before a real event.</p>
    </div>
  </div>
  <a class="btn btn-outline" href="#">Download our free guide to crisis preparation</a>
</section>

<section class="reviews">
  <svg class="reviews-band" width="1200" height="420" viewBox="0 0 1200 420" aria-hidden="true">
    <defs><linearGradient id="reviewGrad" x1="0" y1="0" x2="0" y2="1"><stop offset="0" stop-color="#8c1c42"/><stop offset="1" stop-color="#1d3a6b"/></linearGradient></defs>
    <path d="M0 20 Q600 -40 1200 20 L1200 390 Q600 450 0 390 Z" fill="url(#reviewGrad)"/>
  </svg>
  <h2 class="section-title">Customer review</h2>
  <div class="review-card" style="left:165px">
    <div class="avatar" role="img" aria-label="Customer portrait photo"></div>
    <div><blockquote>“ The training gave our team a clear plan and real confidence when pressure hits.</blockquote><cite>Mara Quill</cite>
      <div class="stars"><svg width="90" height="16" viewBox="0 0 90 16" aria-hidden="true"><g fill="#e3b21a"><polygon points="8,0 10,6 16,6 11,10 13,16 8,12 3,16 5,10 0,6 6,6"/><polygon transform="translate(18)" points="8,0 10,6 16,6 11,10 13,16 8,12 3,16 5,10 0,6 6,6"/><polygon transform="translate(36)" points="8,0 10,6 16,6 11,10 13,16 8,12 3,16 5,10 0,6 6,6"/><polygon transform="translate(54)" points="8,0 10,6 16,6 11,10 13,16 8,12 3,16 5,10 0,6 6,6"/></g><polygon transform="translate(72)" points="8,0 10,6 16,6 11,10 13,16 8,12 3,16 5,10 0,6 6,6" fill="none" stroke="#e3b21a"/></svg></div></div>
  </div>
  <div class="review-card" style="left:460px">
    <div class="avatar" role="img" aria-label="Customer portrait photo"></div>
    <div><blockquote>“ The training gave our team a clear plan and real confidence when pressure hits.</blockquote><cite>Mara Quill</cite>
      <div class="stars"><svg width="90" height="16" viewBox="0 0 90 16" aria-hidden="true"><g fill="#e3b21a"><polygon points="8,0 10,6 16,6 11,10 13,16 8,12 3,16 5,10 0,6 6,6"/><polygon transform="translate(18)" points="8,0 10,6 16,6 11,10 13,16 8,12 3,16 5,10 0,6 6,6"/><polygon transform="translate(36)" points="8,0 10,6 16,6 11,10 13,16 8,12 3,16 5,10 0,6 6,6"/><polygon transform="translate(54)" points="8,0 10,6 16,6 11,10 13,16 8,12 3,16 5,10 0,6 6,6"/></g><polygon transform="translate(72)" points="8,0 10,6 16,6 11,10 13,16 8,12 3,16 5,10 0,6 6,6" fill="none" stroke="#e3b21a"/></svg></div></div>
  </div>
  <div class="review-card" style="left:763px">
    <div class="avatar" role="img" aria-label="Customer portrait photo"></div>
    <div><blockquote>“ The training gave our team a clear plan and real confidence when pressure hits.</blockquote><cite>Mara Quill</cite>
      <div class="stars"><svg width="90" height="16" viewBox="0 0 90 16" aria-hidden="true"><g fill="#e3b21a"><polygon points="8,0 10,6 16,6 11,10 13,16 8,12 3,16 5,10 0,6 6,6"/><polygon transform="translate(18)" points="8,0 10,6 16,6 11,10 13,16 8,12 3,16 5,10 0,6 6,6"/><polygon transform="translate(36)" points="8,0 10,6 16,6 11,10 13,16 8,12 3,16 5,10 0,6 6,6"/><polygon transform="translate(54)" points="8,0 10,6 16,6 11,10 13,16 8,12 3,16 5,10 0,6 6,6"/></g><polygon transform="translate(72)" points="8,0 10,6 16,6 11,10 13,16 8,12 3,16 5,10 0,6 6,6" fill="none" stroke="#e3b21a"/></svg></div></div>
  </div>
  <div class="review-nav">
    <span><svg width="10" height="10" viewBox="0 0 10 10" aria-hidden="true"><path d="M7 1 L3 5 L7 9" fill="none" stroke="#fff" stroke-width="1.5"/></svg></span>
    <span><svg width="10" height="10" viewBox="0 0 10 10" aria-hidden="true"><path d="M3 1 L7 5 L3 9" fill="none" stroke="#fff" stroke-width="1.5"/></svg></span>
  </div>
</section>

<section class="workshops">
  <h2 class="section-title">Workshops</h2>
  <article class="workshop-card" style="left:165px">
    <div class="workshop-photo" role="img" aria-label="Photo of a live workshop with a presenter and audience" style="background:linear-gradient(135deg,#8a7360,#3f342d)"></div>
    <h3>Live Workshops</h3>
    <p>Join a full day session with peers and work through real crisis cases together.</p>
    <a class="btn btn-solid" href="#">Register now</a>
  </article>
  <article class="workshop-card" style="left:467px">
    <div class="workshop-photo" role="img" aria-label="Photo of a person taking an online course at a computer" style="background:linear-gradient(135deg,#dfe5ea,#8d9aa6)"></div>
    <h3>Online Course</h3>
    <p>Learn at your own pace with short video lessons and practical planning tools.</p>
    <a class="btn btn-solid" href="#">Enroll now</a>
  </article>
  <article class="workshop-card" style="left:770px">
    <div class="workshop-photo" role="img" aria-label="Photo of a small team in a private workshop at a laptop" style="background:linear-gradient(135deg,#e9e3da,#9d8b78)"></div>
    <h3>Private Workshop</h3>
    <p>A tailored session for your own team, built around your products and risks.</p>
    <a class="btn btn-solid" href="#">Get a quote</a>
  </article>
  <a class="btn btn-outline" href="#">Register for a workshop</a>
</section>

<section class="simulations">
  <div class="sim-illustration" role="img" aria-label="Illustration of a hand holding a phone showing star ratings and comments"></div>
  <h2 class="sim-title">Crisis Simulations</h2>
  <p class="sim-sub">The closest your team will get to a real crisis without being in one!</p>
  <div class="sim-item" style="top:190px">
    <div class="sim-icon"><span><svg width="22" height="22" viewBox="0 0 22 22" aria-hidden="true"><rect x="2" y="3" width="18" height="13" rx="3" fill="none" stroke="#fff" stroke-width="2"/><path d="M6 16 L5 20 L10 16" fill="#fff"/></svg></span></div>
    <div><h3>Practice your social media response</h3><p>Handle a live stream of posts and comments and learn how to reply with care.</p></div>
  </div>
  <div class="sim-item" style="top:305px">
    <div class="sim-icon"><span><svg width="26" height="22" viewBox="0 0 26 22" aria-hidden="true"><circle cx="13" cy="6" r="4" fill="#fff"/><circle cx="5" cy="9" r="3" fill="#fff"/><circle cx="21" cy="9" r="3" fill="#fff"/><path d="M6 20 Q13 8 20 20 Z M0 20 Q5 12 9 17 Z M17 17 Q21 12 26 20 Z" fill="#fff"/></svg></span></div>
    <div><h3>Role-playing all key stakeholders</h3><p>Face media, regulators, staff and customers played by our experienced team.</p></div>
  </div>
  <div class="sim-item" style="top:420px">
    <div class="sim-icon"><span><svg width="24" height="22" viewBox="0 0 24 22" aria-hidden="true"><ellipse cx="12" cy="9" rx="10" ry="7" fill="#fff"/><path d="M5 14 L3 20 L10 15" fill="#fff"/></svg></span></div>
    <div><h3>Instant feedback &amp; coaching on your response</h3><p>Get clear notes on what worked and what to improve right after each round.</p></div>
  </div>
  <a class="btn btn-outline" href="#">Get a quote</a>
</section>

<section class="different">
  <svg class="different-band" width="1200" height="510" viewBox="0 0 1200 510" aria-hidden="true">
    <path d="M0 40 Q600 -30 1200 40 L1200 510 L0 510 Z" fill="#1d3a6b"/>
  </svg>
  <h2>What makes us different?</h2>
  <p>We combine years of food and consumer goods experience with hands-on training. Our team has managed real recalls and brand crises, so every session is practical, current and built for the pressure senior managers face when their reputation is on the line.</p>
  <a class="btn" href="#">Read more</a>
  <div class="different-photo" role="img" aria-label="Photo of a team working together around a table with laptops"></div>
</section>

<section class="contact">
  <h2 class="section-title">Get in touch</h2>
  <form class="contact-form">
    <div class="field">First Name</div>
    <div class="field">Last Name</div>
    <div class="field">Email Address</div>
    <div class="field">Phone Number</div>
    <div class="field field-wide">Message</div>
  </form>
  <a class="btn btn-solid" href="#">Submit</a>
</section>

<footer class="site-footer">
  <nav class="footer-nav">
    <a href="#">About us</a><a href="#">Workshops</a><a href="#">Online course</a><a href="#">Simulations</a><a href="#">Contact us</a><a href="#">Blog</a>
  </nav>
  <p class="copyright">© 2019 Company Name &nbsp;All right reserved</p>
</footer>

</body>
</html>
```